Restaurant Facility Equipment & Store Maintenance/

I need a flyer showing commercial/industrial kitchen equipment photos we work on Hot Equipment & Cold Equipment and offer many services. see attached highlights

```html
<!DOCTYPE html>
<html lang="en">
<head>
<meta charset="utf-8">
<title>Restaurant Facility Equipment &amp; Store Maintenance Flyer</title>
<link rel="stylesheet" href="https://fonts.googleapis.com/css2?family=Bebas+Neue&family=Montserrat:wght@400;500;600;700&display=swap">
<style>
:root{
  --blue:#0d5b8a;
  --orange:#e8941f;
  --white:#ffffff;
  --ink:#141414;
  --stage:#e6e6e6;
}
*{margin:0;padding:0;box-sizing:border-box}
html,body{width:1200px;height:667px;overflow:hidden;background:var(--stage)}
.flyer-frame{position:absolute;left:374px;top:13px;width:452px;height:640px;box-shadow:0 6px 14px rgba(0,0,0,.25)}
.flyer{position:absolute;left:0;top:0;width:854px;height:1207px;background:var(--white);transform:scale(.5295);transform-origin:0 0;overflow:hidden;font-family:'Montserrat',sans-serif;color:var(--ink)}
.hero-photo{position:absolute;left:0;top:0;width:854px;height:430px}
.title{position:absolute;left:44px;top:52px;font-family:'Bebas Neue',sans-serif;font-size:74px;line-height:67px;color:var(--blue);letter-spacing:.5px;font-weight:400}
.title .accent{color:var(--orange)}
.subtitle{position:absolute;left:44px;top:262px;font-size:18.8px;font-weight:500;line-height:21px}
.headline{position:absolute;left:44px;top:334px;font-family:'Bebas Neue',sans-serif;font-size:52px;line-height:47px;color:var(--orange);font-weight:400}
.intro{position:absolute;left:44px;top:436px;width:758px;font-size:18.6px;font-weight:500;line-height:20.6px;text-align:justify}
.services-band{position:absolute;left:0;top:539px;width:623px;height:526px;background:var(--orange)}
.side-band{position:absolute;left:623px;top:539px;width:231px;height:526px;background:var(--blue)}
.service-list{position:absolute;left:44px;top:553px;list-style:none;color:var(--white);font-size:14.6px;line-height:26.4px}
.service-list li{display:flex;align-items:center}
.service-list .tick{width:14px;height:14px;flex:none;margin-right:3px}
.service-list .indent{padding-left:17px}
.gallery-photo{position:absolute;left:590px;width:212px;height:114px;border:2px solid var(--white)}
.call-label{position:absolute;left:44px;top:1090px;font-family:'Bebas Neue',sans-serif;font-size:46px;line-height:40px;color:var(--blue)}
.phone{position:absolute;left:44px;top:1130px;font-size:48px;font-weight:700;line-height:50px;color:var(--orange);letter-spacing:-1px}
.contact-band{position:absolute;left:445px;top:1097px;width:409px;height:75px}
.contact-text{position:absolute;left:517px;top:1102px;color:var(--white);font-size:21px;font-weight:500;line-height:29px}
</style>
</head>
<body>
<svg width="0" height="0" style="position:absolute" aria-hidden="true">
  <symbol id="tick" viewBox="0 0 16 16">
    <circle cx="8" cy="8" r="6.5" fill="none" stroke="#fff" stroke-width="1.5"/>
    <path d="M4.6 8.2l2.4 2.5 4.6-5.3" fill="none" stroke="#fff" stroke-width="1.9" stroke-linecap="round" stroke-linejoin="round"/>
  </symbol>
</svg>
<div class="flyer-frame">
<div class="flyer">
  <svg class="hero-photo" viewBox="0 0 854 430">
    <defs>
      <linearGradient id="heroTone" x1="0" y1="0" x2="1" y2="1">
        <stop offset="0" stop-color="#b98a56"/>
        <stop offset=".5" stop-color="#9fb0bb"/>
        <stop offset="1" stop-color="#2c3a4c"/>
      </linearGradient>
    </defs>
    <polygon points="678,0 854,0 854,418 540,208" fill="var(--blue)"/>
    <polygon role="img" aria-label="Technician in cap and gloves servicing a commercial refrigeration unit" points="700,0 854,0 854,398 562,206" fill="url(#heroTone)"/>
  </svg>

  <h1 class="title">Restaurant Facility<br>Equipment <span class="accent">&amp; Store</span><br><span class="accent">Maintenance</span></h1>
  <p class="subtitle">Installation, Rebuilds, OSHA Inspection, and Preventive<br>Maintenance Services for Denver Metro and Surrounding Areas.</p>
  <h2 class="headline">We handle everything from<br>the front door to the back door.</h2>
  <p class="intro">We offer hot and cold equipment repair, cleaning, maintenance, handyman work, drywall, painting, door closers, floors, and ceiling tiles. For any need in your restaurant, call us and we will send a skilled technician to manage all your commercial and industrial facility requirements.</p>

  <div class="services-band"></div>
  <div class="side-band"></div>

  <ul class="service-list">
    <li><svg class="tick"><use href="#tick"/></svg>CKSTA Certified Technicians</li>
    <li><svg class="tick"><use href="#tick"/></svg>Round-the-clock emergency services</li>
    <li><svg class="tick"><use href="#tick"/></svg>Customers who subscribe to preventive maintenance</li>
    <li class="indent">services receive a reduced rate on hourly labor charges.</li>
    <li><svg class="tick"><use href="#tick"/></svg>Original equipment manufacturer (OEM) parts</li>
    <li><svg class="tick"><use href="#tick"/></svg>30-day warranty on all OEM parts installed</li>
    <li><svg class="tick"><use href="#tick"/></svg>Equipment Cleaning &amp; Rebuilds</li>
    <li><svg class="tick"><use href="#tick"/></svg>Used equipment available for purchase or rental</li>
    <li><svg class="tick"><use href="#tick"/></svg>Specialized Programs for Preventive Maintenance of Equipment</li>
    <li><svg class="tick"><use href="#tick"/></svg>Installation and Repair of Restaurant Equipment</li>
    <li><svg class="tick"><use href="#tick"/></svg>Repair or replace restaurant furniture</li>
    <li><svg class="tick"><use href="#tick"/></svg>Comprehensive licensed electrical contractor services</li>
    <li class="indent">for both interior and exterior projects, including lighting</li>
    <li class="indent">system upgrades.</li>
    <li><svg class="tick"><use href="#tick"/></svg>Building Graffiti Removal Services</li>
    <li><svg class="tick"><use href="#tick"/></svg>Hot &amp; Cold Equipment</li>
    <li><svg class="tick"><use href="#tick"/></svg>Food Service Trucks</li>
    <li><svg class="tick"><use href="#tick"/></svg>We repair floors, walls, counters, décor, signage,</li>
    <li class="indent">parking lots, dumpsters, and more. If you have it, we probably fix it.</li>
  </ul>

  <div class="gallery-photo" style="top:557px;background:linear-gradient(135deg,#8a9299,#3a4450)" role="img" aria-label="Technician cleaning a stainless steel kitchen grill"></div>
  <div class="gallery-photo" style="top:682px;background:linear-gradient(135deg,#dcdfe2,#7e858c)" role="img" aria-label="Commercial stainless steel kitchen with ovens and prep tables"></div>
  <div class="gallery-photo" style="top:807px;background:linear-gradient(135deg,#6f8fa3,#b4563a)" role="img" aria-label="Worker pressure washing graffiti off a brick wall"></div>
  <div class="gallery-photo" style="top:932px;background:linear-gradient(180deg,#2d4e8a,#1a2436)" role="img" aria-label="Food service truck parked at dusk"></div>

  <p class="call-label">Call Now Today!</p>
  <p class="phone">555-019-24760</p>

  <svg class="contact-band" viewBox="0 0 409 75" aria-hidden="true">
    <polygon points="30,0 409,0 409,75 0,75" fill="var(--blue)"/>
  </svg>
  <p class="contact-text">www.kitchencrewpro.com<br>info@kitchencrewpro.com</p>
</div>
</div>
</body>
</html>
```